K & R Acre Works. Business card design

We need a business card designed for a new business. We have a bulldozer and tractor service. We clear land and make wildlife food plots. We provide disking, bush hogging, and site prep services.
I have attached an image of a business card that I like and would like my business cards to look similar.

Target Market(s)

anyone needing bulldozer and/or tractor services

Industry/Entity Type

Business

Contact Information for Business Card

K & R Acre Works, Operated by 7-T-Ranch
Wade Colton
601-472-3358
wcr4817@fieldmail-example.com

Font styles to use
Sans Serif

Colors

Designer to choose colors to be used in the design.

Requirements
Must have
• image of tractor and bulldozer
• Land Clearing
• Wildlife food plots
• Bush Hogging
• Disking
• Site prep
Nice to have
• i have included a image of a business card that i like. I would like mine to be similar.

```html
<!DOCTYPE html>
<html lang="en">
<head>
<meta charset="utf-8">
<title>K &amp; R Acre Works – Business Card</title>
<link href="https://fonts.googleapis.com/css2?family=Oswald:wght@300;400;500;600&display=swap" rel="stylesheet">
<style>
  :root {
    --page-bg: #e9e6e1;
    --card-dark: #182014;
    --foliage: #33452a;
    --foliage-light: #56683f;
    --machine-red: #c0381f;
    --machine-orange: #d9542a;
    --accent-red: #d6202b;
    --accent-red-dark: #9e121b;
    --ink-light: #f4f4f2;
    --ink-muted: #d3d6cf;
  }
  * { margin: 0; padding: 0; box-sizing: border-box; }
  html, body {
    width: 1200px; height: 1023px; overflow: hidden;
    background: var(--page-bg);
  }
  body {
    display: flex; align-items: center; justify-content: center;
    font-family: "Oswald", sans-serif;
  }
  .business-card {
    position: relative;
    width: 1000px; height: 572px;
    border-radius: 18px;
    overflow: hidden;
    background: var(--card-dark);
    box-shadow: 0 18px 40px rgba(0,0,0,.25);
    color: var(--ink-light);
  }
  .photo-area {
    position: absolute; inset: 0;
    background:
      radial-gradient(ellipse 30% 40% at 90% 15%, var(--foliage-light), rgba(86,104,63,0) 75%),
      radial-gradient(ellipse 35% 35% at 15% 85%, var(--foliage), rgba(51,69,42,0) 75%),
      linear-gradient(160deg, var(--foliage) 0%, var(--card-dark) 45%, var(--foliage) 100%);
  }
  .photo-machines {
    position: absolute; left: 290px; top: 150px; width: 600px; height: 330px;
    border-radius: 40px;
    background:
      radial-gradient(ellipse 45% 55% at 30% 55%, var(--machine-orange), rgba(217,84,42,0) 80%),
      radial-gradient(ellipse 40% 45% at 72% 40%, var(--machine-red), rgba(192,56,31,0) 85%),
      linear-gradient(90deg, rgba(192,56,31,.35), rgba(192,56,31,.55) 50%, rgba(192,56,31,.3));
    filter: blur(6px);
  }
  .photo-shade {
    position: absolute; inset: 0;
    background: linear-gradient(90deg, rgba(12,16,10,.7) 0%, rgba(12,16,10,.3) 40%, rgba(12,16,10,.15) 100%);
  }
  .company {
    position: absolute; left: 60px; top: 60px;
  }
  .company-name {
    font-weight: 500; font-size: 46px; letter-spacing: 1px;
    text-transform: uppercase; line-height: 1;
  }
  .company-operator {
    margin-top: 12px;
    font-weight: 300; font-size: 20px; letter-spacing: 6px;
    text-transform: uppercase; color: var(--ink-muted);
  }
  .owner-name {
    position: absolute; right: 70px; top: 186px;
    font-weight: 600; font-size: 64px; letter-spacing: 1px;
    text-transform: uppercase; line-height: 1;
  }
  .divider {
    position: absolute; left: 110px; right: 60px; top: 272px;
    height: 2px; background: var(--ink-light);
  }
  .contact {
    position: absolute; left: 110px; top: 294px;
    list-style: none; font-weight: 300; font-size: 27px;
  }
  .contact li { display: flex; align-items: center; gap: 14px; line-height: 44px; }
  .contact svg { width: 20px; height: 20px; flex: none; }
  .services {
    position: absolute; list-style: none;
    font-weight: 400; font-size: 21px; letter-spacing: .5px;
    text-transform: uppercase; line-height: 30px;
  }
  .services-primary { left: 110px; top: 396px; }
  .services-secondary { left: 620px; top: 300px; }
  .wave { position: absolute; left: 0; bottom: 0; width: 1000px; height: 572px; }
</style>
</head>
<body>
  <article class="business-card">
    <div class="photo-area" role="img" aria-label="Photograph of a red tractor and bulldozer working among green trees">
      <div class="photo-machines"></div>
    </div>
    <div class="photo-shade"></div>

    <header class="company">
      <h1 class="company-name">K &amp; R Acre Works</h1>
      <p class="company-operator">Operated by 7-T-Ranch</p>
    </header>

    <h2 class="owner-name">Wade Colton</h2>
    <div class="divider"></div>

    <ul class="contact">
      <li>
        <svg viewBox="0 0 24 24" fill="none" stroke="currentColor" stroke-width="2"><path d="M5 3h4l2 5-3 2a12 12 0 0 0 6 6l2-3 5 2v4a2 2 0 0 1-2 2A18 18 0 0 1 3 5a2 2 0 0 1 2-2z"/></svg>
        601-472-3358
      </li>
      <li>
        <svg viewBox="0 0 24 24" fill="none" stroke="currentColor" stroke-width="2"><rect x="3" y="5" width="18" height="14"/><path d="M3 5l9 8 9-8"/></svg>
        wcr4817@fieldmail-example.com
      </li>
    </ul>

    <ul class="services services-primary">
      <li>Land Clearing</li>
      <li>Wildlife Food Plots</li>
    </ul>
    <ul class="services services-secondary">
      <li>Bush Hogging</li>
      <li>Disking - Site Prep</li>
    </ul>

    <svg class="wave" viewBox="0 0 1000 572" preserveAspectRatio="none" aria-hidden="true">
      <path d="M0 572 L0 540 C 260 548, 520 520, 700 470 C 830 434, 920 420, 1000 424 L1000 572 Z" fill="var(--accent-red)"/>
      <path d="M0 558 C 300 564, 560 540, 740 494 C 860 464, 940 452, 1000 454 L1000 572 L0 572 Z" fill="var(--accent-red-dark)" opacity=".5"/>
      <path d="M0 532 C 260 540, 520 512, 700 462 C 830 426, 920 412, 1000 416" fill="none" stroke="#ffffff" stroke-width="5"/>
    </svg>
  </article>
</body>
</html>
```